Corporate brochure design 4 pages

Hi,

We are a real estate company based in Europe.

We have almost finalized a rebranding.

We are developing a brand book guidelines (still on working process) to help you undertstand the look and feel of our new CI. I would like to receive proposals of design for a corporate brochure template. I need to receive the Indesign files with full ownership rights to be able to adapt all our documentation with this template.
Regarding the images, you can take gabaris on www.pelvarimages.example. I will be able to take them afterwards.

There will be 4 pages. you will receive the 4 pages on pdf for your consideration with our (almost) actual layout.

- 1st page: cover
- 2nd page: company presentation in french and english
- 3rd page: some market data + graph
- 4th page: 2 retail centers presentation.

In the template, i need to have:
- the paragraph styles in order
- 2 different masters with top/bottom/page number aso.

Please feel free to ask any other questions.

best regards,
Updates

I would like to precise tha t we are active on the commercial real estate sector:

- office transactions (rent /sales)
- property management of administrative and business buildings
- Valuation of properties
- Capital markets (investment advices for selling building)

Industry/Entity Type

Real Estate

Colors

Designer to choose colors to be used in the design.

```html
<!DOCTYPE html>
<html lang="en">
<head>
<meta charset="utf-8">
<title>About us – A team</title>
<link href="https://fonts.googleapis.com/css2?family=Arimo:ital,wght@0,400;0,700;1,400&display=swap" rel="stylesheet">
<style>
  :root {
    --orange: #f26522;
    --ink: #111111;
    --body-grey: #6d6e71;
    --caption-grey: #9a9a9a;
    --paper: #ffffff;
  }
  * { margin: 0; padding: 0; box-sizing: border-box; }
  html, body { width: 848px; height: 1200px; overflow: hidden; background: var(--paper); }
  body { font-family: "Arimo", Arial, sans-serif; position: relative; }

  .page { position: relative; width: 848px; height: 1200px; }

  .column { position: absolute; top: 190px; width: 364px; }
  .column--fr { left: 44px; }
  .column--en { left: 442px; }

  .section-label {
    color: var(--orange);
    font-weight: 700;
    font-size: 22px;
    letter-spacing: 0.3px;
    height: 32px;
    line-height: 24px;
  }
  .section-label--active {
    display: inline-block;
    border-bottom: 3px solid var(--ink);
    padding-right: 2px;
  }

  .headline {
    margin-top: 55px;
    font-weight: 400;
    font-size: 52px;
    line-height: 56px;
    color: var(--ink);
    letter-spacing: 0.5px;
  }

  .lead {
    margin-top: 22px;
    color: var(--orange);
    font-weight: 700;
    font-size: 15.5px;
    line-height: 27px;
    text-align: justify;
  }

  .body-copy {
    margin-top: 27px;
    color: var(--body-grey);
    font-size: 15.5px;
    line-height: 27px;
    text-align: justify;
  }
  .body-copy p + p.gap { margin-top: 27px; }

  /* wrap-around spacers that open room for the team photo */
  .wrap-push { width: 0; height: 308px; }
  .column--fr .wrap-push { float: right; }
  .column--en .wrap-push { float: left; }
  .wrap-room { height: 330px; }
  .column--fr .wrap-room { float: right; clear: right; width: 206px; }
  .column--en .wrap-room { float: left; clear: left; width: 205px; }

  .team-photo {
    position: absolute;
    left: 218px; top: 815px;
    width: 416px; height: 278px;
    background: linear-gradient(160deg, #c9ccce 0%, #9ea3a6 35%, #3b3d42 70%, #1f2024 100%);
  }
  .team-caption {
    position: absolute;
    left: 226px; top: 1099px;
    font-style: italic;
    font-size: 13px;
    color: var(--caption-grey);
  }
  .accent-block {
    position: absolute;
    left: 218px; top: 1121px;
    width: 416px; height: 79px;
    background: var(--orange);
  }
</style>
</head>
<body>
<main class="page">

  <section class="column column--fr" lang="fr">
    <h2 class="section-label">A PROPOS DE NOUS</h2>
    <h1 class="headline">UNE ÉQUIPE</h1>
    <p class="lead">Proposer des services de qualité répondant parfaitement à vos attentes est notre ambition. Elle est partagée par tous les membres de notre équipe.</p>
    <div class="body-copy">
      <div class="wrap-push"></div>
      <div class="wrap-room"></div>
      <p>Notre connaissance du marché luxembourgeois, nos compétences et notre engagement dans les missions qui nous sont confiées font de Meridian Estates l’acteur majeur de l’immobilier d’entreprise au Grand-Duché. Nous sommes fiers de cette position et nous travaillons tous les jours pour la conserver.</p>
      <p>Viser l’excellence suppose de savoir améliorer sans cesse nos prestations pour répondre le plus précisément à vos besoins. Venez nous consulter, vous constaterez que nos collaborateurs prennent le temps de vous écouter pour bien comprendre votre demande. Leur professionnalisme, leur savoir-faire et leur mobilisation nous permettront de trouver la solution.</p>
    </div>
  </section>

  <section class="column column--en" lang="en">
    <h2 class="section-label"><span class="section-label--active">ABOUT US</span></h2>
    <h1 class="headline">A TEAM</h1>
    <p class="lead">Our ambition is to offer quality services that perfectly meet your expectations. This ambition is shared by all members of the team.</p>
    <div class="body-copy">
      <div class="wrap-push"></div>
      <div class="wrap-room"></div>
      <p>Thanks to our knowledge of the Luxembourg market, our skills and our commitment to the missions entrusted to us, Meridian Estates is the undisputed leader in commercial real estate in the Grand Duchy. We are proud of this position and work hard to deserve it every day.</p>
      <p class="gap">Targeting excellence means the constant improvement of our services in order to more accurately meet your needs. When you meet with us, you will find that our employees take the necessary time to listen to you and to correctly understand your need. Their professionalism, know-how and mobilisation will ensure that we find the right solution.</p>
    </div>
  </section>

  <div class="team-photo" role="img" aria-label="Photo of the four team members in dark suits in a modern office"></div>
  <p class="team-caption">Julien Marceau, Olivier Dantec, Paul Keller, Erik Lindqvist</p>
  <div class="accent-block"></div>

</main>
</body>
</html>
```